Corvane Freight Company Business Card Design

We are a company that delivers natural saltwater (from the ocean) to aquarium companies, restaurants and home marine tanks. I would like a new business card to suit.

Must include Name, company name, abn, contact number and website as well as logo (see attached).

Looking for a design that stands out, has a clean but unique appearance.

Double and single sided entries welcome

Business

• Logo

```html
<!DOCTYPE html>
<html lang="en">
<head>
<meta charset="utf-8">
<title>Corvane Freight Company – Business Card</title>
<link href="https://fonts.googleapis.com/css2?family=Source+Sans+3:wght@400;600;700&display=swap" rel="stylesheet">
<style>
  :root {
    --backdrop: #141414;
    --card: #ffffff;
    --card-edge: #d9d9d9;
    --brand-blue: #0b8fd6;
    --name-blue: #1f5fa8;
    --ink: #222222;
    --rule: #3a3a3a;
  }
  * { margin: 0; padding: 0; box-sizing: border-box; }
  html, body {
    width: 1200px; height: 420px; overflow: hidden;
    background: var(--backdrop);
    font-family: "Source Sans 3", "Helvetica Neue", Arial, sans-serif;
  }
  .stage { position: relative; width: 1200px; height: 420px; }
  .card {
    position: absolute; top: 68px; width: 525px; height: 299px;
    background: var(--card); border: 1px solid var(--card-edge);
    border-radius: 22px;
  }
  .card--front { left: 70px; }
  .card--back { left: 632px; }

  .brand {
    position: absolute; color: var(--brand-blue); font-weight: 600;
    line-height: 1.05;
  }
  .card--front .brand { left: 32px; top: 128px; width: 230px; font-size: 30px; }
  .card--back .brand {
    left: 0; right: 0; top: 108px; text-align: center; font-size: 50px;
  }

  .contact { position: absolute; left: 300px; top: 58px; width: 192px; color: var(--ink); }
  .contact__name { color: var(--name-blue); font-weight: 700; font-size: 19px; line-height: 1.1; }
  .contact__title { color: var(--name-blue); font-size: 15px; margin-top: 1px; }
  .contact__rule { height: 1px; background: var(--rule); margin: 9px 0 12px; }
  .contact__line { display: flex; align-items: center; gap: 6px; font-size: 13.5px; margin-bottom: 6px; }
  .contact__line svg { width: 10px; height: 10px; flex: none; }
  .contact__address { font-size: 13.5px; line-height: 1.55; }
  .contact__abn { font-size: 13.5px; margin-top: 12px; }
</style>
</head>
<body>
<main class="stage">
  <section class="card card--front">
    <div class="brand">Corvane Freight Company</div>
    <div class="contact">
      <div class="contact__name">Your Name</div>
      <div class="contact__title">Title</div>
      <div class="contact__rule"></div>
      <div class="contact__line">
        <svg viewBox="0 0 10 10" aria-hidden="true"><path d="M2 1 L4 3 L3 4 Q4.5 6 6 7 L7 6 L9 8 L8 9.2 Q3 8.5 0.8 2 Z" fill="var(--ink)"/></svg>
        <span>123-456-7892</span>
      </div>
      <div class="contact__line">
        <svg viewBox="0 0 10 10" aria-hidden="true"><circle cx="5" cy="5" r="4.3" fill="none" stroke="var(--ink)" stroke-width="1"/><ellipse cx="5" cy="5" rx="1.8" ry="4.3" fill="none" stroke="var(--ink)" stroke-width="0.8"/><path d="M0.7 5 H9.3" stroke="var(--ink)" stroke-width="0.8"/></svg>
        <span>www.corvanefreight.com</span>
      </div>
      <div class="contact__rule"></div>
      <div class="contact__address">Street Name, City Name ,<br>State, Zip Code</div>
      <div class="contact__abn">ABN: 123456789</div>
    </div>
  </section>
  <section class="card card--back">
    <div class="brand">Corvane Freight<br>Company</div>
  </section>
</main>
</body>
</html>
```